Brimlow OrthoLink IT Inc. new website

i need a website for my company which is dedicated to installation and service of computer systems in Dental Offices. I would like for it to encompass a technology feel and professional look. The company deals with all aspects of technology like, Audio Visual, computer systems and networks, Cloud services like data backup, data center. We provide manage services, support and services to Dental Professionals.
Updates

Looking for a Technology font but professional look Added Wednesday, April 20, 2016

Target Market(s)

Dental, Dentist

Industry/Entity Type

Dental

Number of Pages Required

5+ page

Font styles to use
Other font styles liked:
• Futuristic or Techy

Colors
0255a3
ec1f27

Requirements
Must have
• Tabs
Nice to have
• Have no idea maybe some suggestion on your part may help
Should not have
• A professional feel but have a techy look

```html
<!DOCTYPE html>
<html lang="en">
<head>
<meta charset="utf-8">
<title>Brimlow OrthoLink IT Inc.</title>
<link rel="stylesheet" href="https://fonts.googleapis.com/css2?family=Nunito+Sans:wght@400;600;700&family=Lato:wght@700;900&family=Open+Sans:wght@400;600;700&family=Raleway:wght@500&family=Roboto+Condensed:wght@400;700&display=swap">
<style>
:root{
  --blue:#0255a3;
  --black:#0c0c0c;
  --ink:#1c1c1c;
  --muted:#6e6e6e;
  --gray-band:#ececec;
  --card:#efefef;
  --footer:#2a2a2a;
  --footer-text:#b9b9b9;
  --white:#ffffff;
}
*{box-sizing:border-box;margin:0;padding:0}
html,body{width:1200px;height:2757px;overflow:hidden;background:var(--white)}
body{position:relative;font-family:"Open Sans",sans-serif;color:var(--ink)}
.abs{position:absolute}
.heading{font-family:"Nunito Sans",sans-serif;font-weight:400;color:var(--ink);font-size:37px;text-align:center}
.heading span{color:var(--blue)}

/* header */
.site-header{left:0;top:0;width:1200px;height:118px}
.brand{left:79px;top:28px;display:flex;align-items:center;gap:14px;font-family:"Nunito Sans",sans-serif;font-weight:700;font-size:30px;color:var(--blue)}
.brand-mark{width:34px;height:34px;background:var(--blue)}
.contact-chip{top:26px;display:flex;align-items:center;gap:16px}
.chip-icon{width:59px;height:59px;border:2px solid var(--blue);border-radius:50%;display:flex;align-items:center;justify-content:center}
.chip-phone{left:588px;font-family:"Open Sans",sans-serif;font-weight:700;font-size:26px;color:var(--blue)}
.chip-mail{left:860px;font-size:19px;color:var(--blue)}
.header-divider{left:840px;top:34px;width:1px;height:44px;background:#cfcfcf}

/* nav */
.main-nav{left:0;top:118px;width:1200px;height:58px;background:var(--blue);font-family:"Raleway",sans-serif;font-weight:500;font-size:19px;color:var(--white)}
.main-nav .item{position:absolute;top:0;height:58px;line-height:58px;transform:translateX(-50%)}
.main-nav .active{left:77px;width:123px;transform:none;background:var(--black);text-align:center}

/* hero */
.hero{left:0;top:176px;width:1200px;height:521px}
.hero-photo{position:absolute;inset:0;background:linear-gradient(90deg,#ffffff 0%,#f4f6fa 30%,#d9dfe8 55%,#c2cad6 75%,#aeb7c4 100%)}
.hero-photo::after{content:"";position:absolute;left:660px;top:30px;width:230px;height:140px;background:#5b6470;opacity:.55}
.hero-title{left:79px;top:92px;font-family:"Lato",sans-serif;font-weight:900;font-size:42px;line-height:60px;color:var(--black)}
.hero-sub{left:79px;top:215px;font-size:18.5px;line-height:30px;color:var(--ink)}
.btn-solid{background:var(--blue);color:var(--white);font-family:"Roboto Condensed",sans-serif;font-weight:700;text-align:center;border-radius:3px}
.hero-btn{left:77px;top:300px;width:204px;height:62px;line-height:62px;font-size:25px}

/* services */
.services-title{left:0;top:744px;width:1200px}
.service-card{top:810px;width:313px;height:201px;background:var(--card);border-radius:4px;text-align:center}
.service-card svg{margin-top:42px}
.service-card p{margin-top:18px;font-family:"Nunito Sans",sans-serif;font-size:27px;color:var(--ink)}

/* welcome */
.welcome{left:0;top:1084px;width:1200px;height:313px;background:var(--gray-band)}
.welcome .heading{position:absolute;left:0;top:44px;width:1200px}
.welcome-text{position:absolute;left:170px;top:116px;width:860px;text-align:center;font-size:15.5px;line-height:25px;color:var(--muted)}
.btn-outline{position:absolute;left:516px;top:210px;width:168px;height:51px;line-height:49px;border:1.5px solid var(--blue);background:var(--white);color:var(--blue);font-family:"Roboto Condensed",sans-serif;font-size:22px;text-align:center;border-radius:3px}

/* technology */
.tech-title{left:0;top:1443px;width:1200px}
.tech-item{top:1511px;width:340px;text-align:center}
.tech-ring{width:124px;height:124px;border:2px solid var(--blue);border-radius:50%;margin:0 auto;display:flex;align-items:center;justify-content:center}
.tech-item h3{margin-top:20px;font-family:"Nunito Sans",sans-serif;font-weight:400;font-size:21px;line-height:33px;color:var(--ink)}
.tech-item p{margin-top:6px;font-size:15.5px;line-height:25px;color:var(--muted)}

/* contact + testimonials */
.touch{left:0;top:1867px;width:1200px;height:478px;background:var(--gray-band)}
.touch .heading{position:absolute;top:58px;text-align:left;font-size:34px}
.field{position:absolute;left:77px;width:469px;height:43px;background:var(--white);border:1px solid #c9c9c9;font-size:15px;color:#555;padding:10px 8px}
.submit{position:absolute;left:77px;top:377px;width:136px;height:42px;line-height:42px;font-family:"Open Sans",sans-serif;font-weight:400;font-size:21px}
.testimonial{position:absolute;left:635px;width:500px}
.avatar{position:absolute;left:0;top:0;width:124px;height:124px;border-radius:50%;border:3px solid var(--blue);background:radial-gradient(circle at 50% 40%,#d6c7b6 0%,#9aa3ad 70%,#5b6470 100%)}
.quote{position:absolute;left:148px;top:-10px;width:352px;font-size:15.5px;line-height:28px;color:var(--muted)}
.quote b{display:block;margin-top:6px;font-family:"Open Sans",sans-serif;font-weight:700;font-size:13px;color:var(--blue)}

/* support band */
.support-band{left:0;top:2345px;width:1200px;height:85px;background:var(--blue);display:flex;align-items:center;justify-content:center;gap:20px;color:var(--white);font-family:"Nunito Sans",sans-serif;font-size:38px}
.band-phone{width:58px;height:58px;border:2px solid var(--white);border-radius:50%;display:flex;align-items:center;justify-content:center}
.support-band strong{font-family:"Open Sans",sans-serif;font-weight:700;font-size:37px}

/* footer */
.site-footer{left:0;top:2430px;width:1200px;height:327px;background:var(--footer);color:var(--footer-text)}
.col{position:absolute;top:26px;width:250px}
.col h4{font-family:"Nunito Sans",sans-serif;font-weight:400;font-size:20px;color:var(--white);margin-bottom:14px}
.links li{list-style:none;font-size:15px;line-height:31px;display:flex;align-items:center;gap:8px}
.links li:first-child{color:var(--white)}
.news p{font-size:14.5px;line-height:23px;color:#dcdcdc;margin-bottom:22px}
.news span{display:block}
.newsletter p{font-size:14px;color:#dcdcdc;margin-bottom:18px}
.news-field{width:234px;height:36px;border:1px solid #9a9a9a;font-size:15px;color:#e6e6e6;padding:7px 8px;margin-bottom:12px}
.subscribe{width:160px;height:40px;line-height:40px;font-family:"Open Sans",sans-serif;font-weight:400;font-size:20px}
.info-row{display:flex;gap:10px;font-size:14.5px;line-height:23px;color:#dcdcdc;margin-bottom:10px}
.info-phone{font-weight:700;font-size:20px;color:var(--white)}
.socials{display:flex;gap:18px;margin-top:12px}
.socials span{width:45px;height:45px;border-radius:50%;background:var(--white)}
.footer-rule{left:79px;top:274px;width:1042px;height:1px;background:#444}
.copyright{left:0;top:288px;width:1200px;text-align:center;font-size:15px;color:#dcdcdc}
.copyright b{color:var(--white)}
</style>
</head>
<body>

<header class="site-header abs">
  <div class="brand abs"><span class="brand-mark"></span>Brimlow OrthoLink IT</div>
  <div class="contact-chip chip-phone abs">
    <span class="chip-icon"><svg width="26" height="26" viewBox="0 0 24 24"><path fill="#0255a3" d="M6.6 10.8a15 15 0 0 0 6.6 6.6l2.2-2.2c.3-.3.7-.4 1-.2 1.1.4 2.3.6 3.6.6.6 0 1 .4 1 1V20c0 .6-.4 1-1 1A17 17 0 0 1 3 4c0-.6.4-1 1-1h3.5c.6 0 1 .4 1 1 0 1.3.2 2.5.6 3.6.1.3 0 .7-.2 1z"/></svg></span>
    123 456 7890
  </div>
  <div class="header-divider abs"></div>
  <div class="contact-chip chip-mail abs">
    <span class="chip-icon"><svg width="26" height="20" viewBox="0 0 26 20"><rect x="1.5" y="1.5" width="23" height="17" rx="2" fill="none" stroke="#0255a3" stroke-width="2"/><path d="M2 3l11 8 11-8" fill="none" stroke="#0255a3" stroke-width="2"/></svg></span>
    info@brimlowortholink.com
  </div>
</header>

<nav class="main-nav abs">
  <span class="item active">HOME</span>
  <span class="item" style="left:265px">ABOUT</span>
  <span class="item" style="left:412px">SERVICES</span>
  <span class="item" style="left:566px">SUPPORT</span>
  <span class="item" style="left:711px">CLIENT</span>
  <span class="item" style="left:838px">BLOG</span>
  <span class="item" style="left:976px">CONTACT</span>
</nav>

<section class="hero abs">
  <div class="hero-photo" role="img" aria-label="Bright modern dental treatment room with a chair, instruments and an X-ray display on the wall"></div>
  <h1 class="hero-title abs">TECHNOLOGY FOR<br>BEST PRACTICE</h1>
  <p class="hero-sub abs">f you view technology as an expense rather than<br>an investment, you haven’t worked with us.</p>
  <div class="hero-btn btn-solid abs">CONTACT US</div>
</section>

<h2 class="heading services-title abs">Our <span>Services</span></h2>
<div class="service-card abs" style="left:77px">
  <svg width="74" height="66" viewBox="0 0 74 66" fill="#0255a3"><rect x="27" y="0" width="20" height="18"/><rect x="35" y="18" width="4" height="12"/><rect x="9" y="28" width="56" height="4"/><rect x="9" y="28" width="4" height="14"/><rect x="35" y="28" width="4" height="14"/><rect x="61" y="28" width="4" height="14"/><rect x="0" y="44" width="22" height="20"/><rect x="26" y="44" width="22" height="20"/><rect x="52" y="44" width="22" height="20"/></svg>
  <p>Manage services</p>
</div>
<div class="service-card abs" style="left:443px">
  <svg width="74" height="66" viewBox="0 0 74 66"><circle cx="28" cy="36" r="16" fill="none" stroke="#0255a3" stroke-width="10" stroke-dasharray="6 4"/><circle cx="28" cy="36" r="6" fill="#0255a3"/><circle cx="58" cy="14" r="9" fill="none" stroke="#0255a3" stroke-width="7" stroke-dasharray="4 3"/><circle cx="58" cy="54" r="9" fill="none" stroke="#0255a3" stroke-width="7" stroke-dasharray="4 3"/></svg>
  <p>Support</p>
</div>
<div class="service-card abs" style="left:810px">
  <svg width="74" height="66" viewBox="0 0 74 66" fill="none" stroke="#0255a3" stroke-width="5" stroke-linecap="round"><path d="M6 50l24-8 16 8 22-16"/><path d="M10 60l24-8 16 8 20-14"/><path d="M44 30c4-10 12-16 20-18"/><circle cx="56" cy="10" r="4"/></svg>
  <p>Dental Professionals</p>
</div>

<section class="welcome abs">
  <h2 class="heading">Welcome to <span>Brimlow OrthoLink IT</span></h2>
  <p class="welcome-text">Lorem Ipsum is simply dummy text of the printing and typesetting industry. Lorem Ipsum has been the industry's standard dummy text ever since the 1500s, when an unknown printer took a galley of type and scrambled it to make a type specimen book.</p>
  <div class="btn-outline">READ MORE</div>
</section>

<h2 class="heading tech-title abs">Our <span>Technology</span></h2>
<div class="tech-item abs" style="left:62px">
  <div class="tech-ring"><svg width="60" height="52" viewBox="0 0 60 52" fill="none" stroke="#0255a3" stroke-width="4"><rect x="3" y="3" width="54" height="34" rx="2"/><path d="M22 49h16M30 37v12"/><rect x="22" y="12" width="16" height="12" fill="#0255a3"/></svg></div>
  <h3>Audio Visual</h3>
  <p>Lorem Ipsum is simply dummy text of the printing and typesetting industry. Lorem Ipsum has been the industry.</p>
</div>
<div class="tech-item abs" style="left:427px">
  <div class="tech-ring"><svg width="66" height="56" viewBox="0 0 66 56" fill="none" stroke="#0255a3" stroke-width="3.5"><rect x="3" y="14" width="26" height="20" rx="2"/><path d="M10 42h12M16 34v8"/><path d="M29 24h12M41 6v44M41 6h6M41 20h6M41 36h6M41 50h6"/><rect x="47" y="2" width="14" height="8"/><rect x="47" y="16" width="14" height="8"/><rect x="47" y="32" width="14" height="8"/><rect x="47" y="46" width="14" height="8"/></svg></div>
  <h3>Computer Systems and<br>Networks</h3>
  <p>Lorem Ipsum is simply dummy text of the printing and typesetting industry. Lorem Ipsum has been the industry.</p>
</div>
<div class="tech-item abs" style="left:793px">
  <div class="tech-ring"><svg width="70" height="56" viewBox="0 0 70 56" fill="none" stroke="#0255a3" stroke-width="3.5"><path d="M18 40H14a11 11 0 0 1 0-22 16 16 0 0 1 30-6 12 12 0 0 1 14 12"/><ellipse cx="48" cy="30" rx="12" ry="5" fill="#0255a3"/><path d="M36 30v18c0 3 5 5 12 5s12-2 12-5V30" fill="#0255a3"/><circle cx="58" cy="46" r="8" fill="#fff"/></svg></div>
  <h3>Cloud Services of Data<br>Backup</h3>
  <p>Lorem Ipsum is simply dummy text of the printing and typesetting industry. Lorem Ipsum has been the industry.</p>
</div>

<section class="touch abs">
  <h2 class="heading" style="left:79px">Get In Touch <span>With Us</span></h2>
  <div class="field" style="top:116px">Enter Name</div>
  <div class="field" style="top:169px">Enter Email</div>
  <div class="field" style="top:221px">Enter Contact No.</div>
  <div class="field" style="top:272px;height:94px">Message</div>
  <div class="submit btn-solid">SUBMIT</div>

  <h2 class="heading" style="left:642px">Client <span>Testimonial</span></h2>
  <div class="testimonial" style="top:115px">
    <div class="avatar" role="img" aria-label="Portrait photo of a client"></div>
    <p class="quote">Lorem Ipsum is simply dummy text of the printing and typesetting industry. Lorem Ipsum has been the industry's standard dummy text.<b>- CLIENT NAME</b></p>
  </div>
  <div class="testimonial" style="top:270px">
    <div class="avatar" role="img" aria-label="Portrait photo of a client"></div>
    <p class="quote">Lorem Ipsum is simply dummy text of the printing and typesetting industry. Lorem Ipsum has been the industry's standard dummy text.<b>- CLIENT NAME</b></p>
  </div>
</section>

<div class="support-band abs">
  BRIMLOW ORTHOLINK IT SUPPORT
  <span class="band-phone"><svg width="26" height="26" viewBox="0 0 24 24"><path fill="#fff" d="M6.6 10.8a15 15 0 0 0 6.6 6.6l2.2-2.2c.3-.3.7-.4 1-.2 1.1.4 2.3.6 3.6.6.6 0 1 .4 1 1V20c0 .6-.4 1-1 1A17 17 0 0 1 3 4c0-.6.4-1 1-1h3.5c.6 0 1 .4 1 1 0 1.3.2 2.5.6 3.6.1.3 0 .7-.2 1z"/></svg></span>
  <strong>123 456 7890</strong>
</div>

<footer class="site-footer abs">
  <div class="col" style="left:79px">
    <h4>Useful Links</h4>
    <ul class="links">
      <li><svg width="14" height="12" viewBox="0 0 14 12" fill="none" stroke="currentColor" stroke-width="2"><path d="M1 1l5 5-5 5M7 1l5 5-5 5"/></svg>Home</li>
      <li><svg width="14" height="12" viewBox="0 0 14 12" fill="none" stroke="currentColor" stroke-width="2"><path d="M1 1l5 5-5 5M7 1l5 5-5 5"/></svg>About</li>
      <li><svg width="14" height="12" viewBox="0 0 14 12" fill="none" stroke="currentColor" stroke-width="2"><path d="M1 1l5 5-5 5M7 1l5 5-5 5"/></svg>Services</li>
      <li><svg width="14" height="12" viewBox="0 0 14 12" fill="none" stroke="currentColor" stroke-width="2"><path d="M1 1l5 5-5 5M7 1l5 5-5 5"/></svg>Support</li>
      <li><svg width="14" height="12" viewBox="0 0 14 12" fill="none" stroke="currentColor" stroke-width="2"><path d="M1 1l5 5-5 5M7 1l5 5-5 5"/></svg>News</li>
      <li><svg width="14" height="12" viewBox="0 0 14 12" fill="none" stroke="currentColor" stroke-width="2"><path d="M1 1l5 5-5 5M7 1l5 5-5 5"/></svg>Contact</li>
    </ul>
  </div>
  <div class="col news" style="left:349px">
    <h4>Latest News</h4>
    <p>Lorem Ipsum is simply dummy text of the printing.<span>21 April 2016</span></p>
    <p>Lorem Ipsum is simply dummy text of the printing.<span>21 April 2016</span></p>
  </div>
  <div class="col newsletter" style="left:619px">
    <h4>Newsletter</h4>
    <p>Subscribe to stay on Brimlow OrthoLink IT.</p>
    <div class="news-field">Enter Name</div>
    <div class="news-field">Enter Email</div>
    <div class="subscribe btn-solid">SUBSCRIBE</div>
  </div>
  <div class="col" style="left:891px;width:240px">
    <h4>Contact Info</h4>
    <div class="info-row"><svg width="14" height="20" viewBox="0 0 14 20" style="flex:none"><path fill="#fff" d="M7 0a7 7 0 0 0-7 7c0 5 7 13 7 13s7-8 7-13a7 7 0 0 0-7-7zm0 10a3 3 0 1 1 0-6 3 3 0 0 1 0 6z"/></svg><span>Lorem Ipsum is simply dummy text of the printing.</span></div>
    <div class="info-row info-phone"><svg width="18" height="18" viewBox="0 0 24 24"><path fill="#fff" d="M6.6 10.8a15 15 0 0 0 6.6 6.6l2.2-2.2c.3-.3.7-.4 1-.2 1.1.4 2.3.6 3.6.6.6 0 1 .4 1 1V20c0 .6-.4 1-1 1A17 17 0 0 1 3 4c0-.6.4-1 1-1h3.5c.6 0 1 .4 1 1 0 1.3.2 2.5.6 3.6.1.3 0 .7-.2 1z"/></svg>123 456 7890</div>
    <div class="info-row"><svg width="18" height="14" viewBox="0 0 26 20"><rect x="1.5" y="1.5" width="23" height="17" rx="2" fill="none" stroke="#fff" stroke-width="2.5"/><path d="M2 3l11 8 11-8" fill="none" stroke="#fff" stroke-width="2.5"/></svg>info@brimlowortholink.com</div>
    <div class="socials"><span></span><span></span><span></span></div>
  </div>
  <div class="footer-rule abs"></div>
  <p class="copyright abs">© <b>BRIMLOW ORTHOLINK IT</b> - 2016. All Rights Reserved.</p>
</footer>

</body>
</html>
```